Residential Remodeling Contractor needs updated business card

I need a new design for my business card.
Name of the company is Ridgefell Construction. I need a card that commands presence, strength, integrity. I have been in business for 28 years. I am a Residential Remodeling Contractor that covers all aspects of a residential remodel and build.

```html
<!DOCTYPE html>
<html lang="en">
<head>
<meta charset="utf-8">
<title>Ridgefell Construction – Business Card</title>
<link rel="stylesheet" href="https://fonts.googleapis.com/css2?family=Libre+Baskerville:wght@700&family=Arimo:wght@400&display=swap">
<style>
  :root {
    --backdrop: #989898;
    --card-white: #ffffff;
    --brand-blue: #173d7a;
    --ink: #3a3a3a;
    --divider: #24448a;
  }
  * { box-sizing: border-box; margin: 0; padding: 0; }
  html, body { width: 1200px; height: 1059px; overflow: hidden; }
  body { background: var(--backdrop); position: relative; font-family: "Arimo", Arial, sans-serif; }

  .card {
    position: absolute;
    width: 690px;
    height: 392px;
    border-radius: 24px;
    overflow: hidden;
  }
  .card--front { left: 256px; top: 89px; background: var(--card-white); }
  .card--back  { left: 254px; top: 569px; background: var(--brand-blue); }

  .front-wave { position: absolute; left: 0; top: 0; width: 690px; height: 392px; }

  .identity {
    position: absolute;
    right: 372px;
    top: 146px;
    text-align: right;
    color: var(--ink);
  }
  .identity__name {
    font-family: "Libre Baskerville", Georgia, serif;
    font-weight: 700;
    font-size: 23px;
    letter-spacing: 0.2px;
    color: var(--brand-blue);
    line-height: 28px;
  }
  .identity__role { font-size: 17px; line-height: 22px; margin-top: 2px; }
  .identity__address { font-size: 17px; line-height: 21px; margin-top: 2px; }

  .divider {
    position: absolute;
    left: 344px;
    top: 150px;
    width: 1.5px;
    height: 90px;
    background: var(--divider);
  }

  .contacts {
    position: absolute;
    left: 367px;
    top: 142px;
    list-style: none;
    color: var(--ink);
    font-size: 17px;
  }
  .contacts li { display: flex; align-items: center; height: 26px; }
  .contacts svg { width: 13px; height: 13px; margin-right: 9px; fill: var(--brand-blue); flex: none; }
  .contacts .web-domain { color: var(--brand-blue); }

  .company-name {
    position: absolute;
    left: 0; right: 0;
    top: 172px;
    text-align: center;
    color: var(--card-white);
    font-family: "Arimo", Arial, sans-serif;
    font-weight: 400;
    font-size: 40px;
    line-height: 48px;
  }
</style>
</head>
<body>

  <section class="card card--front" aria-label="Business card front">
    <svg class="front-wave" viewBox="0 0 690 392" aria-hidden="true">
      <path d="M0 326 Q345 388 690 326 L690 392 L0 392 Z" fill="var(--brand-blue)"/>
      <path d="M41 332 Q342 403 643 334" fill="none" stroke="#ffffff" stroke-width="2"/>
    </svg>

    <div class="identity">
      <p class="identity__name">DANIEL WHITCOMBE</p>
      <p class="identity__role">Owner &amp; Manager</p>
      <p class="identity__address">P.O. Box&nbsp; Street Name<br>Country Name AB, A5B 521</p>
    </div>

    <div class="divider"></div>

    <ul class="contacts">
      <li>
        <svg viewBox="0 0 16 16"><path d="M1 6c0-2 3-4 7-4s7 2 7 4v1h-3V5.5C11 5 9.5 4.8 8 4.8S5 5 4 5.5V7H1zM4 8l1.5-2h5L12 8l1 5H3z"/></svg>
        555 310 2284
      </li>
      <li>
        <svg viewBox="0 0 16 16"><path d="M4.5 0h7a1 1 0 0 1 1 1v14a1 1 0 0 1-1 1h-7a1 1 0 0 1-1-1V1a1 1 0 0 1 1-1zM5 2v10h6V2zm3 11a1 1 0 1 0 0 2 1 1 0 0 0 0-2z"/></svg>
        555-472-19038
      </li>
      <li>
        <svg viewBox="0 0 16 16"><path d="M8 1l7 5v9H1V6zm0 2L3 6.5 8 10l5-3.5zM2.5 8v5.5h11V8L8 12z"/></svg>
        info@ridgefellconstruction.com
      </li>
      <li>
        <svg viewBox="0 0 16 16"><path d="M8 0a8 8 0 1 0 0 16A8 8 0 0 0 8 0zM3 5l3 1 1 3-2 2-1 3a6.5 6.5 0 0 1-1-9zm6-3.3a6.5 6.5 0 0 1 5 9l-2-1-1-3 2-2-2-1z"/></svg>
        <span>www.<span class="web-domain">ridgefellconstruction</span>.com</span>
      </li>
    </ul>
  </section>

  <section class="card card--back" aria-label="Business card back">
    <p class="company-name">Ridgefell Construction</p>
  </section>

</body>
</html>
```